New Corporate Email Signature with Custom GIF KAV Electric LLC & KAV Fire & Security

Project Overview
KAV Electric LLC and KAV Fire & Security are seeking a professional, polished, and technically robust corporate email signature design. The project has two integrated deliverables:
A custom animated GIF representing both sides of our business
A complete corporate email signature layout designed for real-world compatibility (Gmail, Outlook, iOS, Android)
Our brand aesthetic is corporate, conservative, and clean. We value clarity, trust, professionalism, and subtle creativity β€” nothing overly flashy or cartoonish.
This design will be used across the entire company and must be visually aligned with our brand while remaining technically dependable.

PART 1 β€” Animated GIF Requirements
The GIF will be the core visual anchor of the new signature.
It must be clean, smooth, subtle, and optimized for email use.
βš™ Technical Requirements
Max file size: 150–200 KB (smaller is better)
Dimensions: approx 300px width (flexible, but must look good small)
Looping: continuous loop
Style: professional, minimalistic transitions

No rapid flashing or harsh animations
Must export cleanly into a format email clients accept

🎞 GIF Animation Sequence
Phase 1 β€” KAV Electric (KE)
Use the yellow β€œKE” avatar logo (provided).
Animation flow:
KE avatar appears
Full name β€œKAV Electric LLC” slides in, fades in, or otherwise appears smoothly
A scrolling or cycling list of service offerings displays:
EV Charging Stations
Generator & Transformers
Testing & Troubleshooting
LED Lighting Upgrades
After the list is shown, the entire KE segment fades out

Phase 2 β€” KAV Fire & Security (KF)
Use the red β€œKF” avatar logo (provided).
Animation flow mirrors Phase 1:
KF avatar appears
Full name β€œKAV Fire & Security” slides/fades in
Scrolling or cycling list of services displays:
Fire Alarm Upgrades
BQTL 48 Test & Inspect
Security Surveillance Systems
Access Control Systems
Data & Fiber Optic Cabling
Fade out β†’ loop back to KE
Creative Direction

Designers are encouraged to use:
Clean transitions
Soft fades
Professional typography
Modern minimalism
Consistent brand colors
High clarity at small sizes

Avoid:
Busy motion
Hard flashes
Excessive text overlays
Overly long transitions

The goal: a smooth, corporate-grade rotation that fits seamlessly into an email signature.

PART 2 β€” Corporate Email Signature Design

The signature must be visually appealing, brand-aligned, and structurally bulletproof across all major email systems.
πŸ“ Required Elements
πŸ‘€ Left Side Content
Circular headshot (we will supply final photos)
Social media icons with embedded URLs:
Pulse
Reach
Locus Business Profile
Frame

Icons should be clean, modern, and in alignment with brand colors
πŸ“„ Right Side Content
Name
Title
KAV Electric LLC / KAV Fire & Security (depending on user)
Phone number
Email address
License# 52804
Physical office address: 384 Pembrook St, Westwood NJ 07912

Small CTA for newsletter signup (button or micro-banner)

🏒 Branding Assets Provided

You will receive:
KE avatar logo
KF avatar logo
Full-name KE logo
Full-name KF logo

These should be incorporated naturally and professionally.

Design Requirements

Conservative corporate styling

Clean typography

Balanced use of white space

Professional hierarchy

Light and dark mode compatibility preferred

Layout should not rely on one large image

All images should export cleanly for hosting on servers/CDN

Avoid overly tall signatures

The final signature must present as modern, trustworthy, and technically reliable across platforms.

πŸ§ͺ Compatibility Requirements

The signature must display correctly in:

Gmail (web and mobile)

Outlook (desktop & online)

Apple Mail

iPhone Mail

Android mail apps

Designers must avoid DIV-based layouts and instead propose a layout that can be implemented using table-based HTML, which is the industry standard for email compatibility.

You do not need to build the HTML β€” only supply the final layered design (PSD/AI/Figma) plus a clear structural layout that can be converted to HTML later.

πŸ“¦ Deliverables
1. Animated GIF

Final optimized GIF

Source file (After Effects, Photoshop, or equivalent)

Export guidelines so we can reproduce future versions

2. Email Signature Design

Full static design mockup

Modular layout for each employee

Icon set for social media

Newsletter CTA element

Clear spacing, alignment, and typography specifications

All source files (PSD, AI, Figma, etc.)

🧭 Creative Guidance Summary

We want:
βœ” Modern
βœ” Corporate
βœ” Minimalistic
βœ” Professional
βœ” Clean motion
βœ” Consistent branding
βœ” Email-safe elements

We do not want:
✘ Flashy marketing look
✘ Overly colorful or playful styles
✘ Hard-to-read fonts
✘ Heavy animation
✘ Oversized signatures

πŸ›  Tools & Format Flexibility

We allow full creative freedom regarding:

Animation style

Typography choices

Structuring of the two-column layout

How the service lists scroll or cycle

As long as the end result is clean, brand-aligned, professional, and email-compatible.

πŸ’¬ Final Note to Designers

We encourage creativity within the boundaries of corporate professionalism.
This signature will represent our company every time an email is sent β€” it must communicate trust, clarity, expertise, and brand strength.

```html
<!DOCTYPE html>
<html lang="en">
<head>
<meta charset="utf-8">
<title>Daniel Reyes – Email Signature</title>
<link rel="stylesheet" href="https://fonts.googleapis.com/css2?family=Inter:wght@400;500;700&family=Open+Sans:wght@600&display=swap">
<style>
  :root {
    --page-bg: #fafafa;
    --brand-red: #e3192b;
    --brand-red-deep: #c8101f;
    --name-grey: #7a7a7a;
    --text-dark: #2e2e2e;
    --text-grey: #6a6a6a;
    --rule-grey: #a5a5a5;
    --white: #ffffff;
  }
  * { margin: 0; padding: 0; box-sizing: border-box; }
  html, body {
    width: 1200px;
    height: 426px;
    overflow: hidden;
    background: var(--page-bg);
  }
  .signature {
    position: relative;
    width: 1200px;
    height: 426px;
    font-family: "Inter", Arial, sans-serif;
  }
  .headshot {
    position: absolute;
    left: 50px;
    top: 57px;
    width: 178px;
    height: 178px;
    border-radius: 50%;
    background: radial-gradient(circle at 50% 40%, #c79a7e 0%, #8a6652 45%, #c9c9c4 75%, #e4e4e0 100%);
  }
  .identity {
    position: absolute;
    left: 252px;
    top: 44px;
  }
  .person-name {
    font-size: 30px;
    font-weight: 700;
    color: var(--name-grey);
    line-height: 36px;
    letter-spacing: -0.2px;
  }
  .job-line {
    margin-top: 6px;
    font-size: 19.5px;
    font-weight: 700;
    color: var(--text-dark);
    line-height: 26px;
  }
  .job-line .company-short { color: var(--name-grey); }
  .job-line .company-division { color: var(--brand-red); }
  .social-links {
    position: absolute;
    right: 60px;
    top: 88px;
    display: flex;
    gap: 12px;
    font-size: 13px;
    font-weight: 500;
    color: var(--text-grey);
  }
  .social-links a { color: inherit; text-decoration: none; }
  .divider {
    position: absolute;
    left: 252px;
    top: 123px;
    width: 889px;
    height: 1px;
    background: var(--rule-grey);
  }
  .contact-list {
    position: absolute;
    left: 252px;
    top: 152px;
    list-style: none;
    font-size: 20.5px;
    color: var(--text-grey);
  }
  .contact-list li {
    height: 37.5px;
    line-height: 26px;
  }
  .contact-list .label-red { color: var(--brand-red); margin-right: 4px; }
  .contact-list .label-dark { color: var(--text-dark); font-weight: 500; margin-right: 4px; }
  .newsletter-band {
    position: absolute;
    left: 54px;
    top: 310px;
    width: 1093px;
    height: 87px;
    border-radius: 9px;
    overflow: hidden;
    background: linear-gradient(90deg, var(--brand-red) 0%, var(--brand-red-deep) 30%, #b02030 100%);
  }
  .work-gallery {
    position: absolute;
    left: 314px;
    top: 0;
    right: 0;
    bottom: 0;
    background: linear-gradient(90deg,
      rgba(176, 32, 48, 0) 0%,
      #8e4a4e 8%,
      #6d6a66 20%,
      #a99a7e 30%,
      #c7473f 40%,
      #d9d9d6 52%,
      #e2e2e0 60%,
      #d64040 67%,
      #b8b8b8 76%,
      #8f9092 88%,
      #c9c9c9 100%);
  }
  .newsletter-button {
    position: absolute;
    left: 81px;
    top: 27px;
    width: 234px;
    height: 37px;
    border: 1.5px solid var(--white);
    border-radius: 19px;
    font-family: "Open Sans", Arial, sans-serif;
    font-weight: 600;
    font-size: 16px;
    color: var(--white);
    line-height: 34px;
    text-align: center;
    text-decoration: none;
  }
</style>
</head>
<body>
  <table class="signature" role="presentation" style="display:block">
    <tbody style="display:block">
      <tr style="display:block">
        <td style="display:block">
          <div class="headshot" role="img" aria-label="Circular headshot photo of the employee"></div>

          <div class="identity">
            <p class="person-name">Daniel Reyes</p>
            <p class="job-line">Project Manager, <span class="company-short">KAV</span> <span class="company-division">Fire &amp; Security</span></p>
          </div>

          <nav class="social-links" aria-label="Social profiles">
            <a href="#">Pulse</a>
            <a href="#">Frame</a>
            <a href="#">Reach</a>
            <a href="#">Locus</a>
          </nav>

          <div class="divider"></div>

          <ul class="contact-list">
            <li><span class="label-red">P :</span>201-555-0148</li>
            <li><span class="label-red">E :</span> daniel.reyes@kavelectric.com</li>
            <li><span class="label-dark">License</span># 52804</li>
            <li><span class="label-dark">Office</span>384 Pembrook St, Alder Falls OH 07912</li>
          </ul>

          <div class="newsletter-band">
            <div class="work-gallery" role="img" aria-label="Strip of project photos: electrical panels, fire alarm equipment and company service vans"></div>
            <a class="newsletter-button" href="#">Join Our Newsletter</a>
          </div>
        </td>
      </tr>
    </tbody>
  </table>
</body>
</html>
```